LB - WESITE NEEDED PAGE: Clean / Modern / Pro & Dynamic

Lantern-Brokers is a new insurance brokerage firm dealing exclusively with companies (BToB) providing the following property: Liabilities Insurance Insurances Automobile Insurance Insurances Construction% 26amp; Engineering Casualty Workmen 's Compensation Health Insurance Marime% 26amp; Transit Credit Insurance Young, Fast, Proactive and Dynamic we call ourselves Lantern-Brokers because we are a "start-up" willing to make a difference in the market, bringing modernity and speed to our industry, still too bureaucratic / procedural / opaque uninitiated. We need something respecting the colors of our orange logtype; blue; white; black; easy to scroll, with simple information on the company; - who we are - our team (with the pictures) - what we do - what we do - contact us, contact us (google map) Luanda (Angola) Small company, just need something flashy / professional / structured / modern.

Target Market(s)

BtoB; Oil and gas companies; French speaking copying established in Angola, all industrials, factories and importers of goods.

Industry/Entity Type

Insurance Broker

Font styles to use
Sans Serif

Colors

Designer to choose colors to be used in the design.

Requirements
Must have
• We need something respecting the colors of our orange logtype; blue; white; black; easy to scroll, with simple information on the company; - who we are - our team (with the pictures) - what we do - what we do - contact us, contact us (google map) Luanda (Angola) Small company, just need something flashy / professional / structured / modern.
Nice to have
• A page format
Should not have
• WE DO NOT WANT A REFER TO OUR LOGO, but a Home Page for our Website with the basics categories ... >> PLEASE CAREFULLY USE THE RIGHT COLOR OF THE LOGOTYPE which are the ones enclosed Orange / Turquoise / Black as per the business card .

```html
<!DOCTYPE html>
<html lang="en">
<head>
<meta charset="utf-8">
<title>Lantern Insurance Brokers</title>
<link href="https://fonts.googleapis.com/css2?family=Play:wght@400;700&family=Montserrat:wght@400;500;600&family=Raleway:wght@400;500;600&display=swap" rel="stylesheet">
<style>
:root{
  --orange:#f15a24;
  --orange-light:#f7913a;
  --blue:#1a8fe3;
  --blue-dark:#0f77c9;
  --ink:#1b1b1b;
  --text:#333;
  --muted:#9a9a9a;
  --light-bg:#f5f5f5;
  --footer:#0d0d0f;
  --white:#fff;
  --line:#dedede;
}
*{margin:0;padding:0;box-sizing:border-box}
html,body{width:1200px;height:3617px;overflow:hidden;background:var(--white)}
body{position:relative;font-family:"Raleway",sans-serif;color:var(--text)}
.abs{position:absolute}
.center{left:0;width:1200px;text-align:center}

/* header & hero */
.hero{position:absolute;left:0;top:0;width:1200px;height:618px;background:linear-gradient(160deg,#5d6670 0%,#8d7a66 45%,#a98f77 60%,#5e6670 100%)}
.hero-shade{position:absolute;left:0;top:0;width:1200px;height:618px;background:rgba(40,48,58,.35)}
.topbar{position:absolute;left:0;top:0;width:1200px;height:70px;background:rgba(45,55,68,.75)}
.brand{position:absolute;left:147px;top:20px;display:flex;align-items:center;gap:8px;font-family:"Montserrat",sans-serif;font-weight:600;font-size:14px;color:var(--orange)}
.brand-dot{width:26px;height:26px;border-radius:50%;background:var(--blue)}
.nav a{position:absolute;top:29px;font-family:"Montserrat",sans-serif;font-size:11px;font-weight:500;color:var(--white);text-decoration:none;letter-spacing:.3px}
.nav a.active{color:var(--orange)}
.phone{position:absolute;left:936px;top:23px;display:flex;align-items:center;gap:10px;color:var(--white);font-family:"Montserrat",sans-serif;font-size:12px}
.phone-ring{width:26px;height:26px;border:2px solid var(--orange);border-radius:50%;display:flex;align-items:center;justify-content:center}
.hero-title{top:266px;font-family:"Play",sans-serif;font-weight:700;font-size:43px;color:var(--white);letter-spacing:1px;text-shadow:0 2px 6px rgba(0,0,0,.35)}
.hero-sub{top:322px;font-family:"Montserrat",sans-serif;font-size:12.5px;line-height:17px;color:var(--white)}
.btn{position:absolute;height:31px;border-radius:16px;background:linear-gradient(90deg,var(--orange),var(--orange-light));color:var(--white);font-family:"Montserrat",sans-serif;font-size:11px;font-weight:500;display:flex;align-items:center;justify-content:center;letter-spacing:.3px}
.btn-mark{position:absolute;left:-8px;top:-4px;width:30px;height:30px;border-radius:50%;background:var(--blue)}
.notch{position:absolute;left:570px;top:594px;width:60px;height:30px;background:var(--white);border-radius:30px 30px 0 0}
.mouse{position:absolute;left:593px;top:605px;width:13px;height:20px;border:2px solid var(--orange);border-radius:7px}

/* section heads */
.eyebrow{font-family:"Montserrat",sans-serif;font-size:12px;color:var(--blue)}
.heading{font-family:"Play",sans-serif;font-weight:700;font-size:34px;color:var(--ink)}
.rule{position:absolute;left:575px;width:50px;height:2px;background:var(--blue)}
.lede{font-family:"Raleway",sans-serif;font-size:10px;color:var(--muted)}

/* about */
.about-photo{left:159px;top:807px;width:438px;height:295px;background:var(--white);box-shadow:0 2px 10px rgba(0,0,0,.2);padding:8px}
.about-photo div{width:100%;height:100%;background:linear-gradient(135deg,#b8c6d3,#e8ecef 50%,#8f9aa5)}
.about-title{left:636px;top:808px;width:340px;font-family:"Montserrat",sans-serif;font-weight:500;font-size:17px;line-height:23px;color:var(--orange)}
.about-copy{left:636px;top:864px;width:419px;font-size:10px;line-height:19.2px;color:var(--muted);text-align:justify}
.about-stem{left:715px;top:1027px;width:1px;height:38px;background:var(--line)}

/* services */
.services{left:0;top:1172px;width:1200px;height:456px;background:var(--light-bg)}
.svc{position:absolute;width:190px;text-align:center}
.svc svg{display:block;margin:0 auto}
.svc p{margin-top:22px;font-family:"Montserrat",sans-serif;font-weight:500;font-size:12.5px;line-height:17px;color:var(--ink)}
.svc.hot p{color:var(--orange)}

/* testimonial */
.testimonial{left:0;top:1628px;width:1200px;height:442px;background:linear-gradient(120deg,#59657a,#7b7f8a 50%,#a0896f)}
.testimonial-shade{left:0;top:1628px;width:1200px;height:442px;background:rgba(60,72,92,.55)}
.t-light{color:var(--white)}
.avatar{left:563px;top:1797px;width:72px;height:72px;border-radius:50%;border:3px solid var(--white);background:linear-gradient(#c9d3dc,#8697a8)}
.client{left:655px;top:1815px;font-family:"Montserrat",sans-serif;font-size:12px;color:var(--white)}
.client small{display:block;margin-top:4px;font-size:9px;font-style:italic;opacity:.85}
.quote{left:280px;top:1880px;width:640px;text-align:center;font-size:11px;line-height:18px;color:var(--white)}
.dots{left:583px;top:1993px;display:flex;gap:8px}
.dots i{width:6px;height:6px;border-radius:50%;background:var(--white)}
.dots i.on{background:var(--orange)}

/* team */
.card{position:absolute;top:2243px;width:213px;height:309px;background:var(--white);box-shadow:0 1px 6px rgba(0,0,0,.12);text-align:center}
.card-photo{height:181px;background:linear-gradient(#e3e5e8,#c4c8cd 60%,#2d3a55)}
.card h4{margin-top:22px;font-family:"Montserrat",sans-serif;font-weight:500;font-size:12.5px;color:var(--ink)}
.card em{display:block;margin-top:4px;font-family:"Montserrat",sans-serif;font-size:11px;color:var(--orange)}
.card p{margin:8px auto 0;width:180px;font-size:10px;line-height:17px;color:var(--muted)}
.socials-side{position:absolute;left:378px;top:2280px;width:20px;height:88px;background:var(--white);border-radius:0 10px 10px 0;display:flex;flex-direction:column;align-items:center;justify-content:space-around;padding:6px 0}
.socials-side i{width:7px;height:7px;border-radius:50%;background:var(--ink)}

/* contact */
.contact{left:0;top:2618px;width:1200px;height:576px;background:#f8f8f8}
.field{position:absolute;height:42px;background:var(--white);border:1px solid var(--line);padding:13px 11px;font-size:10px;color:var(--ink)}

/* newsletter */
.news{left:0;top:3194px;width:1200px;height:72px;background:var(--blue)}
.news-title{left:198px;top:3213px;font-family:"Play",sans-serif;font-weight:700;font-size:25px;color:var(--white)}
.news-icon{left:151px;top:3212px;width:36px;height:36px;border:2px solid var(--white);border-radius:50%}
.news-input{left:483px;top:3214px;width:354px;height:32px;background:var(--white);padding:10px 10px;font-size:10px;color:var(--ink)}

/* footer */
.footer{left:0;top:3266px;width:1200px;height:314px;background:var(--footer)}
.f-head{font-family:"Play",sans-serif;font-weight:700;font-size:21px;color:var(--white)}
.f-rule{position:absolute;height:1px;background:#333}
.f-links{left:143px;top:3345px;list-style:none;font-family:"Montserrat",sans-serif;font-size:11px;color:var(--white)}
.f-links li{position:relative;padding-left:12px;height:30px}
.f-links li::before{content:"";position:absolute;left:0;top:5px;width:4px;height:4px;border-radius:50%;background:var(--white)}
.f-links li.active{color:var(--orange)}
.f-links li.active::before{background:var(--orange)}
.f-sep{left:342px;top:3300px;width:1px;height:210px;background:#2a2a2a}
.f-item{position:absolute;left:413px;display:flex;gap:12px;color:var(--white);font-size:11px;line-height:16px}
.f-badge{flex:none;width:24px;height:24px;border-radius:3px;background:var(--blue)}
.f-social{left:413px;top:3536px;display:flex;gap:6px}
.f-social i{width:21px;height:21px;border-radius:50%;background:var(--white)}
.map{left:650px;top:3266px;width:550px;height:314px;background:linear-gradient(135deg,#eceae6,#dcdad5 50%,#e9e7e2)}
.map-notch{left:650px;top:3388px;width:0;height:0;border-top:36px solid transparent;border-bottom:36px solid transparent;border-left:26px solid var(--footer)}
.copy{left:0;top:3580px;width:1200px;height:37px;line-height:37px;text-align:center;font-size:11px;color:var(--ink);background:var(--white)}
</style>
</head>
<body>

<!-- hero -->
<div class="hero" role="img" aria-label="Photo of a hand passing house keys above a small wooden house model"><div class="hero-shade"></div></div>
<header class="topbar">
  <div class="brand"><span class="brand-dot"></span>Lantern-Brokers</div>
  <nav class="nav">
    <a class="active" style="left:323px">HOME</a>
    <a style="left:391px">WHO WE ARE</a>
    <a style="left:501px">WHAT WE DO</a>
    <a style="left:611px">TESTIMONIAL</a>
    <a style="left:726px">OUR TEAM</a>
    <a style="left:821px">CONTACT US</a>
  </nav>
  <div class="phone">
    <span class="phone-ring"><svg width="12" height="12" viewBox="0 0 24 24"><path fill="#f15a24" d="M6.6 10.8a15 15 0 006.6 6.6l2.2-2.2a1 1 0 011-.25 11.4 11.4 0 003.6.6 1 1 0 011 1V20a1 1 0 01-1 1A17 17 0 013 4a1 1 0 011-1h3.5a1 1 0 011 1c0 1.25.2 2.45.57 3.57a1 1 0 01-.25 1z"/></svg></span>
    (244) 555 0142
  </div>
</header>
<h1 class="abs center hero-title">LANTERN INSURANCE BROKERS</h1>
<p class="abs center hero-sub">We Are A New Insurance Brokerage Firm Dealing Exclusively<br>With Companies.</p>
<div class="btn" style="left:533px;top:381px;width:133px"><span class="btn-mark"></span>CONTACT US</div>
<div class="notch"></div>
<div class="mouse"></div>

<!-- about -->
<section>
  <p class="abs center eyebrow" style="top:693px">About Us</p>
  <h2 class="abs center heading" style="top:710px">Who We Are</h2>
  <div class="rule" style="top:753px"></div>
  <p class="abs center lede" style="top:766px">Lorem ipsum dolor sit amet, consectetuer adipiscing elit, sed diam nonummy nibh euismod tincidunt ut laoreet dolore magna</p>
  <div class="abs about-photo"><div role="img" aria-label="Photo of a smiling businesswoman signing a document with a client"></div></div>
  <h3 class="abs about-title">WELCOME TO LANTERN INSURANCE BROKERS</h3>
  <p class="abs about-copy">Lorem Ipsum Dolor Sit Amet, Consectetuer Adipiscing Elit, Sed Diam Nonummy Nibh Euismod Tincidunt Ut Laoreet Dolore Magna Aliquam Erat Volutpat. Ut Wisi Enim Ad Minim Veniam, Quis Nostrud Exerci Tation Ullamcorper Suscipit Lobortis Nisl Ut Aliquip Ex Ea Commodo Consequat. Duis Autem Vel Eum Iriure Dolor In Hendrerit In Vulputate Velit Esse Molestie Consequat, Vel Illum Dolore Eu Feugiat Nulla Facilisis At Vero Eros Et Accumsan Et Iusto Odio Dignissim Qui Blandit Praesent Luptatum Zzril Delenit Augue Duis Dolore Te Feugait Nulla Facilisi. Lorem Ipsum Dolor Sit Amet, Consectetuer Adipiscing Elit.</p>
  <div class="abs about-stem"></div>
  <div class="btn" style="left:641px;top:1067px;width:138px"><span class="btn-mark"></span>&nbsp;&nbsp;CONTACT US</div>
</section>

<!-- services -->
<section class="abs services">
  <p class="abs center eyebrow" style="top:68px">Services</p>
  <h2 class="abs center heading" style="top:85px">What We Do</h2>
  <div class="rule" style="top:128px"></div>
  <p class="abs center lede" style="top:144px">Lorem ipsum dolor sit amet, consectetuer adipiscing elit, sed diam nonummy nibh euismod tincidunt ut laoreet dolore magna</p>

  <div class="svc" style="left:114px;top:188px">
    <svg width="140" height="140" viewBox="0 0 140 140"><circle cx="70" cy="70" r="55" fill="#fff"/><circle cx="70" cy="70" r="65" fill="none" stroke="#1a8fe3" stroke-width="6" stroke-dasharray="150 54" transform="rotate(-120 70 70)"/><circle cx="70" cy="70" r="65" fill="none" stroke="#1a8fe3" stroke-width="6" stroke-dasharray="120 290" transform="rotate(60 70 70)"/><g fill="none" stroke="#222" stroke-width="2"><path d="M70 46l14 5v10c0 9-6 15-14 18-8-3-14-9-14-18V51z"/><path d="M70 52v22M60 62h20"/><path d="M48 76l10 10h10M92 76l-10 10H72"/></g></svg>
    <p>Liabilities<br>Insurance</p>
  </div>
  <div class="svc" style="left:309px;top:188px">
    <svg width="140" height="140" viewBox="0 0 140 140"><circle cx="70" cy="70" r="55" fill="#fff"/><circle cx="70" cy="70" r="65" fill="none" stroke="#1a8fe3" stroke-width="6" stroke-dasharray="150 54" transform="rotate(-120 70 70)"/><circle cx="70" cy="70" r="65" fill="none" stroke="#1a8fe3" stroke-width="6" stroke-dasharray="120 290" transform="rotate(60 70 70)"/><g fill="none" stroke="#222" stroke-width="2"><circle cx="70" cy="70" r="22"/><path d="M56 74l4-8h18l4 8v6H56z"/><circle cx="62" cy="80" r="2"/><circle cx="78" cy="80" r="2"/><path d="M84 48a6 6 0 016 10l-6 6-6-6a6 6 0 016-10z"/></g></svg>
    <p>Automobile<br>Insurance</p>
  </div>
  <div class="svc hot" style="left:504px;top:186px">
    <svg width="140" height="140" viewBox="0 0 140 140"><circle cx="70" cy="70" r="55" fill="#fff"/><circle cx="70" cy="70" r="65" fill="none" stroke="#f15a24" stroke-width="6" stroke-dasharray="150 54" transform="rotate(-120 70 70)"/><circle cx="70" cy="70" r="65" fill="none" stroke="#f15a24" stroke-width="6" stroke-dasharray="120 290" transform="rotate(60 70 70)"/><g fill="none" stroke="#f15a24" stroke-width="2"><path d="M50 84h40M54 84V64h32v20M60 64V54h20v10M58 72h24M58 78h24"/><path d="M80 54l8-6"/></g></svg>
    <p>Construction And<br>Engineering</p>
  </div>
  <div class="svc" style="left:698px;top:188px">
    <svg width="140" height="140" viewBox="0 0 140 140"><circle cx="70" cy="70" r="55" fill="#fff"/><circle cx="70" cy="70" r="65" fill="none" stroke="#1a8fe3" stroke-width="6" stroke-dasharray="150 54" transform="rotate(-120 70 70)"/><circle cx="70" cy="70" r="65" fill="none" stroke="#1a8fe3" stroke-width="6" stroke-dasharray="120 290" transform="rotate(60 70 70)"/><g fill="none" stroke="#222" stroke-width="2.5"><path d="M70 46l20 7v12c0 12-8 20-20 25-12-5-20-13-20-25V53z"/><path d="M65 58h10v7h7v10h-7v7H65v-7h-7V65h7z"/></g></svg>
    <p>Casualty Workmen ‘s<br>Compensation Health Insurance</p>
  </div>
  <div class="svc" style="left:893px;top:186px">
    <svg width="140" height="140" viewBox="0 0 140 140"><circle cx="70" cy="70" r="55" fill="#fff"/><circle cx="70" cy="70" r="65" fill="none" stroke="#1a8fe3" stroke-width="6" stroke-dasharray="150 54" transform="rotate(-120 70 70)"/><circle cx="70" cy="70" r="65" fill="none" stroke="#1a8fe3" stroke-width="6" stroke-dasharray="120 290" transform="rotate(60 70 70)"/><g fill="none" stroke="#222" stroke-width="2"><rect x="48" y="54" width="44" height="22"/><circle cx="70" cy="65" r="6"/><circle cx="58" cy="84" r="5" fill="#222"/><circle cx="82" cy="84" r="5" fill="#222"/></g></svg>
    <p>Marime And Transit<br>Credit</p>
  </div>
</section>

<!-- testimonial -->
<section>
  <div class="abs testimonial" role="img" aria-label="Photo of hands stopping a row of falling wooden dominoes"></div>
  <div class="abs testimonial-shade"></div>
  <p class="abs center t-light" style="top:1694px;font-family:Montserrat,sans-serif;font-size:12px">Testimonial</p>
  <h2 class="abs center heading t-light" style="top:1708px">What Our Clients Say</h2>
  <p class="abs center t-light" style="top:1760px;font-size:10px">Lorem ipsum dolor sit amet, consectetuer adipiscing elit, sed diam nonummy nibh euismod tincidunt ut laoreet dolore magna</p>
  <div class="abs avatar" role="img" aria-label="Client portrait"></div>
  <div class="abs client">Clients Name<small>- Designer</small></div>
  <p class="abs quote">Lorem ipsum dolor sit amet, consectetuer adipiscing elit, sed diam nonummy nibh euismod tincidunt ut laoreet dolore magna aliquam erat volutpat. Ut wisi enim ad minim veniam, quis nostrud exerci tation ullamcorper suscipit lobortis nisl ut aliquip ex ea commodo consequat. Duis autem vel eum iriure dolor in hendrerit in vulputate velit esse molestie consequat, vel illum dolore eu feugiat nulla facilisis at vero eros et accumsan et iusto odio dignissim qui blandit praesent luptatum zzril delenit augue duis dolore te feugait nulla facilisi.</p>
  <div class="abs dots"><i></i><i class="on"></i><i></i></div>
</section>

<!-- team -->
<section>
  <p class="abs center eyebrow" style="top:2133px">Our Team</p>
  <h2 class="abs center heading" style="top:2147px">Lantern insurance Team</h2>
  <div class="rule" style="top:2190px"></div>
  <p class="abs center lede" style="top:2207px">Lorem ipsum dolor sit amet, consectetuer adipiscing elit, sed diam nonummy nibh euismod tincidunt ut laoreet dolore magna</p>
  <div class="card" style="left:143px"><div class="card-photo" role="img" aria-label="Team member portrait"></div><h4>Your Name</h4><em>General Manager</em><p>Lorem ipsum dolor sit amet, rtetuer adipiscinger elit werr werr veniam werwerr ererwer.</p></div>
  <div class="card" style="left:378px"><div class="card-photo" role="img" aria-label="Team member portrait"></div><h4>Your Name</h4><em>General Manager</em><p>Lorem ipsum dolor sit amet, rtetuer adipiscinger elit werr werr veniam werwerr ererwer.</p></div>
  <div class="socials-side"><i></i><i></i><i></i></div>
  <div class="card" style="left:612px"><div class="card-photo" role="img" aria-label="Team member portrait"></div><h4>Your Name</h4><em>General Manager</em><p>Lorem ipsum dolor sit amet, rtetuer adipiscinger elit werr werr veniam werwerr ererwer.</p></div>
  <div class="card" style="left:846px"><div class="card-photo" role="img" aria-label="Team member portrait"></div><h4>Your Name</h4><em>General Manager</em><p>Lorem ipsum dolor sit amet, rtetuer adipiscinger elit werr werr veniam werwerr ererwer.</p></div>
</section>

<!-- contact -->
<section class="abs contact">
  <p class="abs center eyebrow" style="top:69px">Get in Touch</p>
  <h2 class="abs center heading" style="top:86px">Contact Us</h2>
  <div class="rule" style="top:129px"></div>
  <p class="abs center lede" style="top:152px">Lorem ipsum dolor sit amet, consectetuer adipiscing elit, sed diam nonummy nibh euismod tincidunt ut laoreet dolore magna</p>
  <div class="field" style="left:143px;top:192px;width:449px">First Name*</div>
  <div class="field" style="left:609px;top:192px;width:451px">Last Name*</div>
  <div class="field" style="left:143px;top:245px;width:449px">Email*</div>
  <div class="field" style="left:609px;top:245px;width:451px">Company Name*</div>
  <div class="field" style="left:143px;top:298px;width:449px">Your Tittle*</div>
  <div class="field" style="left:609px;top:298px;width:451px">Phone*</div>
  <div class="field" style="left:143px;top:350px;width:914px;height:96px">Message*</div>
  <div class="btn" style="left:533px;top:475px;width:138px"><span class="btn-mark"></span>&nbsp;&nbsp;&nbsp;SUBMIT</div>
</section>

<!-- newsletter -->
<section>
  <div class="abs news"></div>
  <div class="abs news-icon"></div>
  <h3 class="abs news-title">Newsletter Signup</h3>
  <svg class="abs" style="left:438px;top:3210px" width="24" height="40" viewBox="0 0 24 40"><path d="M3 2l18 18L3 38" fill="none" stroke="#fff" stroke-width="1.5"/></svg>
  <div class="abs news-input">Your e-mail</div>
  <div class="btn" style="left:860px;top:3214px;width:122px;height:32px">SIGN UP</div>
</section>

<!-- footer -->
<footer>
  <div class="abs footer"></div>
  <h3 class="abs f-head" style="left:143px;top:3306px">QUICK LINK</h3>
  <div class="abs f-rule" style="left:143px;top:3336px;width:160px"></div>
  <ul class="abs f-links">
    <li class="active">HOME</li><li>WHO WE ARE</li><li>WHAT WE DO</li><li>TESTIMONIAL</li><li>OUR TEAM</li><li>CONTACT US</li>
  </ul>
  <div class="abs f-sep"></div>
  <h3 class="abs f-head" style="left:413px;top:3306px">GET IN TOUCH</h3>
  <div class="abs f-rule" style="left:413px;top:3336px;width:200px"></div>
  <div class="f-item" style="top:3352px"><span class="f-badge"></span><div><span style="font-size:15px;font-family:Montserrat,sans-serif">Lantern Insurance</span><br><span style="font-size:10px">Lorem Ipsum Dolor Sit Amet,<br>Adipiscinger Elit Werr.</span></div></div>
  <div class="f-item" style="top:3423px;align-items:center"><span class="f-badge"></span>+244 555 0142</div>
  <div class="f-item" style="top:3479px;align-items:center"><span class="f-badge"></span>hello@lanternbrokers.example</div>
  <div class="abs f-social"><i></i><i></i><i></i></div>
  <div class="abs map" role="img" aria-label="Street map of the office location in Luanda"></div>
  <div class="abs map-notch"></div>
  <svg class="abs" style="left:991px;top:3360px" width="22" height="32" viewBox="0 0 22 32"><path d="M11 0a11 11 0 0111 11c0 8-11 21-11 21S0 19 0 11A11 11 0 0111 0z" fill="#e8231f"/><circle cx="11" cy="11" r="4" fill="#fff"/></svg>
  <p class="abs copy">Copyright 2019 Lantern Insurance Brokers. All Rights Reserved.</p>
</footer>

</body>
</html>
```